Local price comparison site needs a new design

We need new, prettier and especially more efficient, design for local (Slovak Republic) price comparison site. The old one (www.tulvenko.sk) is kind of ugly, but more importantly, it doesn't work for consumer audience (performance indicators are kind of bad). We've started something already, but we're just a bunch of amateurs in this area.

Our first attempt is in the attached file. Colors are such because of the logo (which is dark blue and the only given thing at the moment). The design is a combination and inspired by two other similar sites here:
www.brombilo.sk
www.plutavek.cz

We tried, but we're not designers...

Industry/Entity Type

Consumer

Colors

Designer to choose colors to be used in the design.

Requirements
Must have
• Efficient design from performance perspective (we want people to click a lot, content will be attractive enough, we don't want the design to be in the way, but support this)
Vertical banners stripe on the (right) side (see both old and our attempt at new design)
We will need several pages designed (main, category page, product page, search page), but I am not sure how to indicate this in the parameters of the project details
Nice to have
• Please make it simple and easy to read for consumers
Visual design with big pictures

```html
<!DOCTYPE html>
<html lang="en">
<head>
<meta charset="utf-8">
<title>tulvenko.sk – price comparison</title>
<link rel="stylesheet" href="https://fonts.googleapis.com/css2?family=Open+Sans:wght@300;400;600;700&display=swap">
<style>
:root{
  --page:#eceef3;
  --white:#ffffff;
  --blue:#2f6fd0;
  --blue-dark:#1f58b4;
  --heading:#2f6cb4;
  --text:#333a44;
  --muted:#5d6672;
  --line:#dde1e8;
  --dark-panel:#47484b;
  --orange:#f08a24;
}
*{box-sizing:border-box;margin:0;padding:0}
html,body{width:903px;height:1200px;overflow:hidden}
body{background:var(--page);font-family:"Open Sans",sans-serif;color:var(--text);position:relative;font-size:8px}
a{color:inherit;text-decoration:none}
.abs{position:absolute}
.top-links{right:98px;top:11px;font-size:7.5px;color:var(--muted)}
.top-links span{margin:0 4px;color:#aab}
.logo{left:97px;top:36px;display:flex;align-items:center;gap:6px;font-size:24px;font-weight:700;color:var(--blue-dark);letter-spacing:-.5px}
.logo i{width:16px;height:16px;border-radius:50%;background:var(--blue);display:block}
.search{left:339px;top:32px;width:284px;height:32px;background:var(--white);border:1px solid var(--line);border-radius:4px;display:flex;align-items:center;padding:0 3px 0 9px;justify-content:space-between}
.search span{color:#9aa1ab;font-size:7.5px}
.btn{background:linear-gradient(#4b8be6,var(--blue-dark));color:#fff;font-weight:600;font-size:10px;border-radius:3px;display:flex;align-items:center;justify-content:center;border:1px solid #1b4e9f}
.search .btn{width:68px;height:24px}
.tags{left:340px;top:70px;font-size:7.5px;color:var(--muted)}
.sidebar{left:98px;top:94px;width:163px;background:var(--white);border:1px solid var(--line);border-radius:3px;overflow:hidden}
.sidebar h3{background:linear-gradient(#3b7fdf,var(--blue-dark));color:#fff;font-size:10px;font-weight:700;height:31px;display:flex;align-items:center;justify-content:space-between;padding:0 8px}
.sidebar h3 b{width:11px;height:11px;border-radius:50%;background:#fff;display:block}
.sidebar li{list-style:none;height:27.2px;display:flex;align-items:center;border-bottom:1px solid var(--line);font-size:7.5px;padding-left:8px}
.sidebar li:last-child{border:0}
.sidebar li::before{content:"";width:4px;height:4px;border-radius:50%;background:var(--blue);margin-right:17px}
.slider{left:278px;top:93px;width:345px;height:169px;background:var(--white);border:1px solid var(--line);border-radius:3px}
.ph{display:block}
.slider .ph{height:145px;background:linear-gradient(135deg,#d9cfc2,#b9b1a8 55%,#e8e6e2)}
.slider p{font-size:7.5px;padding:7px 8px;display:flex;justify-content:space-between}
.dots i{display:inline-block;width:6px;height:6px;border-radius:50%;background:#888;margin-left:2px}
.dots i:first-child{background:var(--blue)}
.section-title{font-size:10.5px;font-weight:700;color:var(--heading)}
.card{width:106px;height:118px;background:var(--white);border:1px solid var(--line);border-radius:4px;display:flex;align-items:center;justify-content:center}
.card .ph{width:56px;height:86px;border-radius:4px}
.plist{font-size:7.5px;line-height:15px}
.plist a:first-child{color:var(--heading)}
.plist a{display:block}
.bar{left:278px;top:521px;width:345px;height:29px;background:var(--white);border:1px solid var(--line);font-size:7.5px;display:flex;align-items:center;justify-content:space-between;padding:0 10px}
.brands{left:278px;top:561px;width:345px;height:49px;background:var(--white);border:1px solid var(--line);display:flex;align-items:center;justify-content:space-around;padding:0 10px}
.brands i{display:block;height:12px;border-radius:2px;background:#b9c7dc}
.cols{font-size:7.5px;line-height:18px}
.cols h4{font-size:10.5px;color:var(--heading);font-weight:700;margin-bottom:4px}
.app{left:279px;top:780px;width:343px;height:125px;background:linear-gradient(100deg,#3a4a3a,#6d7b52 45%,#c8b7a5 75%,#9aa7b3);border:1px solid var(--line)}
.app h2{position:absolute;left:18px;top:34px;color:#fff;font-weight:300;font-size:16px;line-height:16px}
.app h2 b{font-weight:600;font-size:19px}
.app .btn{position:absolute;left:18px;top:84px;width:91px;height:24px;font-size:8.5px}
.office{left:640px;top:93px;width:165px;height:451px;background:var(--dark-panel)}
.office h2{color:#fff;font-weight:300;font-size:25px;line-height:33px;padding:43px 0 0 14px}
.office .v{color:#fff;font-size:8.5px;padding:6px 0 0 14px}
.office .v span{color:var(--orange)}
.office .n{color:#fff;font-size:7px;padding:22px 0 0 14px}
.office .ph{position:absolute;left:0;top:165px;width:165px;height:286px;background:linear-gradient(160deg,#8a6a48,#5a3c24 55%,#3d2a1a)}
.office .ph small{position:absolute;right:10px;bottom:12px;color:#cbb;font-size:7px;font-weight:300}
.bmx{left:640px;top:573px;width:165px;height:331px;background:linear-gradient(170deg,#5d8fbf,#a8b97d 45%,#6e7a3a 70%,#151515 88%)}
.footer{left:0;top:915px;width:903px;height:225px;background:var(--white)}
.footer .cols{position:absolute;top:8px;line-height:18px}
.footer .cols h4{margin-bottom:16px}
.bottom{left:0;top:1140px;width:903px;height:60px;background:var(--page);border-top:1px solid var(--line)}
.bottom .logo{top:18px;font-size:18px}
.bottom p{position:absolute;right:98px;top:25px;font-size:8.5px;color:var(--muted)}
</style>
</head>
<body>
<div class="abs top-links">Your cart <span>|</span> Orders <span>|</span> SMS Gateway <span>|</span> Webmail <span>|</span> Add shop <span>|</span> My Profile <span>|</span> Log in</div>
<div class="abs logo">tulvenko.sk<i></i></div>
<div class="abs search"><span>Search the Product</span><a class="btn">Search</a></div>
<a class="abs btn" style="left:662px;top:36px;width:67px;height:24px">Login</a>
<a class="abs btn" style="left:739px;top:36px;width:66px;height:24px">Sign Up</a>
<div class="abs tags">Tags : Neque ,porro quisquam, est qui,dolorem ipsum ,quia dolor ..etc</div>

<nav class="abs sidebar">
  <h3>See All Categories <b></b></h3>
  <ul>
    <li>Mobiles &amp; Tablets</li><li>Computers, Laptops &amp; Gaming</li><li>TVs , Audio/Video &amp; Movies</li>
    <li>Cameras, Lenses &amp; Accessories</li><li>Appliances</li><li>Men and Women Clothing</li><li>Footwear</li>
    <li>Watches, Bags &amp; Sunglasses</li><li>Jewellery &amp; Gold Coins</li><li>Perfumes, Beauty &amp; Hygiene</li>
    <li>Home, Kitchen &amp; Furnishing</li><li>Sports,Fitness &amp; Health</li><li>Toys, Kidswear &amp; Babycare</li>
    <li>Books, Stationery &amp; Hobbies</li><li>Automotive</li>
  </ul>
</nav>

<div class="abs slider">
  <div class="ph" role="img" aria-label="Family playing a motion game in a bright living room"></div>
  <p>Neque porro quisquam est qui dolorem ipsum quia dolor sit amet... <span class="dots"><i></i><i></i><i></i><i></i></span></p>
</div>

<div class="abs section-title" style="left:279px;top:288px">Featured Product</div>
<svg class="abs" style="left:601px;top:285px" width="22" height="14" viewBox="0 0 22 14"><path d="M7 2 2 7l5 5M15 2l5 5-5 5" fill="none" stroke="#333" stroke-width="1.8"/></svg>

<div class="abs card" style="left:278px;top:313px"><span class="ph" role="img" aria-label="Smartphone" style="width:42px;background:linear-gradient(#2a2f36,#5f87b5 50%,#2a2f36)"></span></div>
<div class="abs card" style="left:400px;top:313px"><span class="ph" role="img" aria-label="Exam book cover" style="width:66px;border-radius:0;background:linear-gradient(#4a2036,#2d1422)"></span></div>
<div class="abs card" style="left:517px;top:313px"><span class="ph" role="img" aria-label="DSLR camera" style="width:86px;height:62px;background:linear-gradient(#3a3a3a,#111)"></span></div>

<div class="abs plist" style="left:279px;top:437px"><a>View All Mobiles</a><a>Veltra</a><a>Korvin</a><a>Sanuko</a><a>Pexa</a></div>
<div class="abs plist" style="left:402px;top:437px"><a>View All  Books</a><a>Exam Books</a><a>Academic Books</a><a>Technology Books</a><a>School Books</a></div>
<div class="abs plist" style="left:518px;top:437px"><a>View All Camera’s</a><a>DSLRs</a><a>Starters Kit</a><a>Mirrorless</a><a>SLTs</a></div>

<div class="abs bar">TV, Audio, Video , Digital Photography, Cameras , Office , Computer , Telephone ..etc
<svg width="11" height="9" viewBox="0 0 11 9"><path d="M1 1l3.5 3.5L1 8M6 1l3.5 3.5L6 8" fill="none" stroke="#555" stroke-width="1.4"/></svg></div>

<div class="abs brands"><i style="width:60px"></i><i style="width:52px"></i><i style="width:54px"></i><i style="width:56px"></i><i style="width:42px"></i></div>

<div class="abs cols" style="left:279px;top:632px"><h4>Lifestyle</h4>Fashion<br>Beauty<br>Health<br>Gifts<br>Handbags<br>Jewelry</div>
<div class="abs cols" style="left:399px;top:632px"><h4>Automotive</h4>Tires<br>Rims<br>Car Audio<br>Oils<br>Accessories<br>Tuning</div>
<div class="abs cols" style="left:518px;top:632px"><h4>Hobbies</h4>Breeding<br>Fishing<br>Crafting<br>Collecting<br>Sports</div>

<div class="abs app" role="img" aria-label="Hand holding a phone with a shopping app, runner in background">
  <h2>Free Apps to<br><b>Download</b></h2>
  <a class="btn">Learn More &gt;&gt;</a>
</div>

<aside class="abs office">
  <h2>OFFICE*<br>FURNITURE</h2>
  <div class="v">VIEW ALL <span>NEW PRODUCTS</span></div>
  <div class="n">* category with column left + right</div>
  <div class="ph" role="img" aria-label="Wooden desk with laptop and lamp"><small>© Norvald Studio</small></div>
</aside>
<aside class="abs bmx" role="img" aria-label="BMX rider jumping with bike, sponsor banner"></aside>

<footer class="abs footer">
  <div class="cols" style="left:279px"><h4>About Us</h4>Who We Are<br>We are seeing<br>Downloads<br>Contact<br>Press<br>Terms<br>of registration Terms<br>Sitemap</div>
  <div class="cols" style="left:398px"><h4>For transactions</h4>Add / edit shop, service<br>XML feed for e-shops<br>Awards<br>Banners and Links<br>Paid services<br>inclusive programs<br>Affiliate Program<br>Price list<br>F.AQ for shops</div>
  <div class="cols" style="left:518px"><h4>For visitors</h4>Contests<br>Interpretation gifts<br>Career<br>F.AQ visitors<br>Secure Shopping<br>Shop<br>and Service Companies<br>Wholesalers<br>How to choose?</div>
</footer>
<div class="abs bottom">
  <div class="abs logo">tulvenko.sk<i></i></div>
  <p>Tulvenko.sk largest shopping area on the Web Copyright © 2010-2013. All rights reserved.</p>
</div>
</body>
</html>
```